Marlowe Group needs a business card

I would like the card to be simple but modern and elegant.
I like black and white.
or black and gold.
we are a private finance lender and also are involved in property and property developments.

please look at the business card photos i provided i would like M.G only one one side and all the other details on the other side use fonts that tie in with my theme.

Industry/Entity Type

Finance

Contact Information for Business Card

Marlowe Group (M.G) Daniel Marlowe M: 0413586207 E: danmarl@inboxmail.test

Font styles to use
Other font styles liked:
• Use fonts that would reflect our business

Colors
000000
ffffff

Requirements
Must have
• one side of details
• other side has either M.G or Marlowe Group like in the photos provided

```html
<!DOCTYPE html>
<html lang="en">
<head>
<meta charset="utf-8">
<title>Marlowe Group – Business Card</title>
<link rel="stylesheet" href="https://fonts.googleapis.com/css2?family=Saira+Semi+Condensed:wght@800&family=Nunito+Sans:wght@800&family=Didact+Gothic&display=swap">
<style>
  :root {
    --backdrop: #d9d9dc;
    --card: #000000;
    --ink: #ffffff;
    --shadow: rgba(0, 0, 0, 0.25);
  }
  * { margin: 0; padding: 0; box-sizing: border-box; }
  html, body { width: 1200px; height: 800px; overflow: hidden; }
  body {
    background: var(--backdrop);
    display: flex;
    flex-direction: column;
    align-items: center;
    justify-content: center;
    gap: 40px;
  }
  .card {
    width: 600px;
    height: 343px;
    background: var(--card);
    color: var(--ink);
    border-radius: 4px;
    box-shadow: 0 10px 28px var(--shadow);
    position: relative;
    overflow: hidden;
  }
  /* Back side: company name */
  .card--back { display: flex; align-items: center; justify-content: center; }
  .company-name {
    font-family: "Saira Semi Condensed", "Arial Narrow", sans-serif;
    font-weight: 800;
    font-size: 48px;
    letter-spacing: 2px;
    text-transform: uppercase;
    white-space: nowrap;
  }
  /* Front side: monogram + details */
  .card--front {
    display: flex;
    align-items: center;
    padding-left: 44px;
    padding-right: 24px;
  }
  .monogram {
    flex: none;
    font-family: "Saira Semi Condensed", "Arial Narrow", sans-serif;
    font-weight: 800;
    font-size: 92px;
    line-height: 1;
    white-space: nowrap;
  }
  .divider {
    flex: none;
    width: 2px;
    height: 230px;
    background: var(--ink);
    margin: 0 22px 0 22px;
  }
  .details {
    flex: none;
    display: flex;
    flex-direction: column;
    gap: 14px;
    white-space: nowrap;
  }
  .detail-row { display: flex; align-items: center; gap: 14px; }
  .detail-icon { width: 26px; height: 26px; flex: none; }
  .person-name {
    font-family: "Nunito Sans", sans-serif;
    font-weight: 800;
    font-size: 24px;
    line-height: 1;
  }
  .person-title {
    font-family: "Didact Gothic", sans-serif;
    font-size: 12px;
    margin-top: 4px;
  }
  .contact-text {
    font-family: "Didact Gothic", sans-serif;
    font-size: 17px;
    letter-spacing: 1px;
  }
</style>
</head>
<body>
  <section class="card card--back" aria-label="Business card back">
    <h1 class="company-name">Marlowe Group</h1>
  </section>

  <section class="card card--front" aria-label="Business card front">
    <div class="monogram">M.G</div>
    <div class="divider"></div>
    <div class="details">
      <div class="detail-row">
        <svg class="detail-icon" viewBox="0 0 28 28" aria-hidden="true">
          <circle cx="14" cy="9" r="6" fill="#fff"/>
          <path d="M3 27 C3 19 8 16 14 16 C20 16 25 19 25 27 Z" fill="#fff"/>
        </svg>
        <div>
          <div class="person-name">Daniel Marlowe</div>
          <div class="person-title">Position/ Title</div>
        </div>
      </div>
      <div class="detail-row">
        <svg class="detail-icon" viewBox="0 0 28 28" aria-hidden="true">
          <path d="M3 11 C3 5 25 5 25 11 L20 12 L19 9 C16 8 12 8 9 9 L8 12 Z" fill="#fff"/>
          <path d="M6 24 L8 14 L20 14 L22 24 Z" fill="#fff"/>
          <circle cx="14" cy="19" r="3" fill="#000"/>
        </svg>
        <span class="contact-text">0413586207</span>
      </div>
      <div class="detail-row">
        <svg class="detail-icon" viewBox="0 0 28 28" aria-hidden="true">
          <rect x="2" y="6" width="24" height="16" fill="none" stroke="#fff" stroke-width="2"/>
          <path d="M2 6 L14 16 L26 6" fill="none" stroke="#fff" stroke-width="2"/>
        </svg>
        <span class="contact-text">danmarl@inboxmail.test</span>
      </div>
    </div>
  </section>
</body>
</html>
```